Corvane Capital Business Cards

These are professional business cards that are for my family office.
Put fake emails and phone numbers as of now until I finalize those components. This family office controls my families investments, assets, and future. The cards should be professional.
..
.
.
.
I just uploaded another variation of a logo I would like to see as a business card to I am inbeteen which logo to use

Target Market(s)

business

Industry/Entity Type

business

Contact Information for Business Card

Professional, wealth related, finance related.

Requirements
Must have
• Logo

```html
<!DOCTYPE html>
<html lang="en">
<head>
<meta charset="utf-8">
<title>Corvane Capital Business Cards</title>
<link rel="stylesheet" href="https://fonts.googleapis.com/css2?family=Playfair+Display:wght@400&family=Arimo:wght@400&display=swap">
<style>
  :root {
    --backdrop: #c9c9c9;
    --card-dark: #1f1f20;
    --card-mid: #2b2b2c;
    --gold: #c2a66b;
    --white: #f4f4f2;
  }
  * { margin: 0; padding: 0; box-sizing: border-box; }
  html, body {
    width: 1200px;
    height: 788px;
    overflow: hidden;
    background: var(--backdrop);
  }
  .canvas {
    position: relative;
    width: 1200px;
    height: 788px;
    display: flex;
    align-items: center;
    justify-content: center;
    gap: 40px;
  }
  .card {
    position: relative;
    width: 540px;
    height: 309px;
    border-radius: 22px;
    background: linear-gradient(135deg, var(--card-mid) 0%, var(--card-dark) 60%, #262627 100%);
    box-shadow: 0 10px 24px rgba(0, 0, 0, 0.28);
    overflow: hidden;
  }
  .brand-name {
    font-family: "Playfair Display", serif;
    font-weight: 400;
    color: var(--white);
    letter-spacing: 0.06em;
    text-transform: uppercase;
    white-space: nowrap;
  }
  .brand-dot {
    display: inline-block;
    background: var(--gold);
    vertical-align: middle;
  }

  /* Front: contact details */
  .card-front .brand {
    position: absolute;
    left: 44px;
    top: 40px;
    display: flex;
    align-items: center;
    gap: 12px;
  }
  .card-front .brand-dot { width: 14px; height: 14px; }
  .card-front .brand-name { font-size: 24px; }

  .person {
    position: absolute;
    left: 44px;
    top: 118px;
    display: flex;
    gap: 16px;
  }
  .person-bar {
    width: 16px;
    height: 52px;
    background: var(--gold);
    margin-top: 4px;
  }
  .person-name {
    font-family: "Playfair Display", serif;
    font-size: 25px;
    color: var(--gold);
    letter-spacing: 0.05em;
    text-transform: uppercase;
    line-height: 1.15;
  }
  .person-title {
    font-family: "Arimo", sans-serif;
    font-size: 17px;
    color: var(--white);
    margin-top: 4px;
  }
  .contact-list {
    position: absolute;
    left: 76px;
    top: 200px;
    list-style: none;
  }
  .contact-item {
    display: flex;
    align-items: center;
    gap: 10px;
    font-family: "Arimo", sans-serif;
    font-size: 16px;
    color: var(--white);
    line-height: 29px;
  }
  .contact-icon { width: 14px; height: 14px; flex: none; }

  /* Back: brand */
  .card-back {
    display: flex;
    align-items: center;
    justify-content: center;
    gap: 16px;
  }
  .card-back .brand-dot { width: 18px; height: 18px; }
  .card-back .brand-name { font-size: 40px; }
</style>
</head>
<body>
<main class="canvas">
  <section class="card card-front" aria-label="Business card front">
    <div class="brand">
      <span class="brand-dot"></span>
      <span class="brand-name">Corvane Capital</span>
    </div>
    <div class="person">
      <div class="person-bar"></div>
      <div>
        <div class="person-name">Daniel Reyes</div>
        <div class="person-title">CEO/Founder</div>
      </div>
    </div>
    <ul class="contact-list">
      <li class="contact-item">
        <svg class="contact-icon" viewBox="0 0 16 16" aria-hidden="true"><path fill="var(--gold)" d="M3.2 1.5l2.3 2.6-1.3 1.6c.9 2 2.4 3.5 4.4 4.4l1.6-1.3 2.6 2.3-1.4 2.2C6.5 13.1 2.9 9.5 1 4.6z"/></svg>
        <span>(555) 014-3820</span>
      </li>
      <li class="contact-item">
        <svg class="contact-icon" viewBox="0 0 16 16" aria-hidden="true"><rect x="1" y="3.5" width="14" height="9.5" rx="1" fill="var(--gold)"/><path d="M1.5 4.5L8 9l6.5-4.5" fill="none" stroke="var(--card-dark)" stroke-width="1.3"/></svg>
        <span>DanielR@corvanecapital.com</span>
      </li>
      <li class="contact-item">
        <svg class="contact-icon" viewBox="0 0 16 16" aria-hidden="true"><circle cx="8" cy="8" r="6.5" fill="var(--gold)"/><path d="M1.5 8h13M8 1.5c-3 3.5-3 9.5 0 13M8 1.5c3 3.5 3 9.5 0 13" fill="none" stroke="var(--card-dark)" stroke-width="1"/></svg>
        <span>www.corvanecapital.com</span>
      </li>
    </ul>
  </section>

  <section class="card card-back" aria-label="Business card back">
    <span class="brand-dot"></span>
    <span class="brand-name">Corvane Capital</span>
  </section>
</main>
</body>
</html>
```